Flyer-Design für Heizungsbau
Zielgruppe
Wir sind ein junges, kompetentes und zertifiziertes Fachbetrieb und bieten Beratung, Fachplanung und fachmännische Installation von Wärmepumpen, Klimaanlagen und Lüftungsanlagen. Unsere Zielgruppe sind Eigentümer von Bestandsgebäuden oder Neubauten (hauptsächlich Privatkunden in mittlerem oder höherem Alter), welche eine Heizungssanierung für Heizkostenreduzierung oder neue Heizinstallation (Wärmepumpen), und/oder mehr Komfort bzw. Luftqualität in ihren Zuhause wünschen (Klima und Lüftung).
Aufgabenstellung
Schwerpunkte: 1. Ersparnis an Heizkosten, 2. Wohlgefühl und 3. Klimaschutz

```html
<!DOCTYPE html>
<html lang="de">
<head>
<meta charset="utf-8">
<title>Kühlwerk Flyer</title>
<link href="https://fonts.googleapis.com/css2?family=Varela+Round&family=Roboto+Condensed:wght@300;400;700&display=swap" rel="stylesheet">
<style>
:root{
  --navy:#173f86;
  --blue:#3f9ad6;
  --sky:#5db3e6;
  --band:#59ade2;
  --ink:#3a3f4a;
  --paper:#ffffff;
  --stage:#e4e4e6;
  --head:"Varela Round",sans-serif;
  --body:"Roboto Condensed",sans-serif;
}
*{margin:0;padding:0;box-sizing:border-box}
html,body{width:1200px;height:2350px;overflow:hidden;background:var(--stage)}
.flyer{position:absolute;top:615px;width:560px;height:1120px;background:var(--paper);overflow:hidden;box-shadow:0 4px 14px rgba(0,0,0,.18)}
.flyer--front{left:20px}
.flyer--back{left:620px}

/* front */
.headline{position:absolute;left:22px;top:16px;font-family:var(--head);font-weight:400;font-size:53px;line-height:56px;color:var(--blue)}
.headline .lead{color:var(--navy)}
.benefits{position:absolute;left:0;top:201px;width:560px;height:72px;background:var(--band);display:flex;align-items:center;justify-content:center;gap:14px;font-family:var(--body);font-size:19px;color:#fff}
.benefits span{display:flex;align-items:center;gap:6px}
.benefits span::before{content:"";width:14px;height:14px;border-radius:50%;background:var(--navy);border:2px solid #fff}
.hero-photo{position:absolute;left:0;top:273px;width:560px;height:560px;background:linear-gradient(160deg,#8a8e93 0%,#c9c3bd 30%,#eef1f4 60%,#d9e2ea 100%)}
.services{position:absolute;left:0;top:830px;width:560px;height:153px;background:var(--band)}
.service{position:absolute;top:-56px;width:166px;text-align:center;color:#fff}
.service .icon{width:84px;height:84px;margin:0 auto;border-radius:50%;background:var(--navy);border:3px solid #fff;display:flex;align-items:center;justify-content:center}
.service h3{font-family:var(--head);font-weight:400;font-size:26px;color:var(--navy);margin-top:6px}
.service p{font-family:var(--body);font-weight:300;font-size:13.5px;line-height:17px;margin-top:5px}
.footer{position:absolute;left:0;top:983px;width:560px;height:137px}
.contact{position:absolute;font-family:var(--body);font-size:15px;color:var(--navy)}
.contact li{list-style:none;display:flex;align-items:center;gap:10px;height:28px;white-space:nowrap}
.brand{position:absolute;display:flex;align-items:center;gap:14px;font-family:var(--head);font-size:42px;color:var(--blue);white-space:nowrap}
.brand::before{content:"";width:50px;height:50px;border-radius:50%;background:var(--navy)}

/* back */
.intro{position:absolute;left:28px;top:30px;width:508px;font-family:var(--body);font-size:14px;line-height:23px;color:var(--ink)}
.intro b{color:var(--navy)}
.intro em{font-style:normal;color:var(--blue)}
.promise-area{position:absolute;left:0;top:188px;width:560px;height:795px;background:radial-gradient(ellipse at 30% 40%,#d9f0fc 0%,#8ccdf1 45%,var(--sky) 100%)}
.photo-circle{position:absolute;border-radius:50%}
.photo-couple{left:-10px;top:198px;width:245px;height:245px;background:linear-gradient(150deg,#6b6058,#d8cfc6 50%,#f3f1ef)}
.photo-unit{left:300px;top:260px;width:258px;height:258px;background:radial-gradient(circle at 40% 50%,#f2f2f2 0%,#9a9a9a 45%,#4b4b4d 100%);transform:translateX(10px)}
.photo-woman{left:282px;top:670px;width:262px;height:262px;background:linear-gradient(160deg,#234b5e,#6ea5a8 40%,#e9dcc0 70%,#f4f4f2)}
.promise{position:absolute;left:33px;top:456px;width:248px;color:#fff;font-family:var(--body)}
.promise h2{font-family:var(--head);font-weight:400;font-size:26px;white-space:nowrap;margin-bottom:6px}
.promise h3{font-family:var(--head);font-weight:400;font-size:19px;color:var(--navy);margin-top:8px}
.promise p{font-size:14px;line-height:18px;font-weight:300}
.offer{position:absolute;left:5px;top:812px;width:228px;height:228px;border-radius:50%;background:#fff;box-shadow:0 6px 14px rgba(0,0,0,.25);transform:rotate(-8deg);padding-top:40px;text-align:center}
.offer p{font-family:var(--head);font-size:18px;line-height:21px;color:var(--blue)}
.offer ul{margin:20px 0 0 14px;text-align:left;font-family:var(--head);font-size:15px;color:var(--navy)}
.offer li{list-style:none;display:flex;align-items:center;gap:8px;height:27px;white-space:nowrap}
</style>
</head>
<body>

<section class="flyer flyer--front">
  <h1 class="headline"><span class="lead">Ihr Fachbetrieb für</span><br>Klimaanlagen und<br>Installation</h1>
  <div class="benefits"><span>Ersparnis an Heizkosten</span><span>Wohlgefühl</span><span>Klimaschutz</span></div>
  <div class="hero-photo" role="img" aria-label="Foto: Mann schläft zufrieden an ein Klimagerät gelehnt, Fernbedienung in der Hand"></div>
  <div class="services">
    <div class="service" style="left:16px">
      <div class="icon"><svg width="44" height="44" viewBox="0 0 24 24"><path fill="#fff" d="M21 6.5a5 5 0 0 1-6.6 4.7L6 19.6a2 2 0 0 1-2.8-2.8l8.4-8.4A5 5 0 0 1 17.5 3l-3 3 .7 2.8 2.8.7z"/></svg></div>
      <h3>Installation</h3>
      <p>Wir installieren Ihre Klimaanlage fachmännisch und mit höchster Präzision</p>
    </div>
    <div class="service" style="left:197px">
      <div class="icon"><svg width="42" height="42" viewBox="0 0 24 24"><path fill="#fff" d="M2 3h3l2.6 11h10.6L21 6H7.2L6.6 4H2zM9 17a2 2 0 1 0 0 4 2 2 0 0 0 0-4zm8 0a2 2 0 1 0 0 4 2 2 0 0 0 0-4z"/></svg></div>
      <h3>Verkauf</h3>
      <p>Bei uns erhalten Sie Ihr Klimagerät zu einem günstigen Preis. Wir verkaufen nur hochwertige Anlagen</p>
    </div>
    <div class="service" style="left:378px">
      <div class="icon"><svg width="44" height="44" viewBox="0 0 24 24"><path fill="#fff" d="M21 6.5a5 5 0 0 1-6.6 4.7L6 19.6a2 2 0 0 1-2.8-2.8l8.4-8.4A5 5 0 0 1 17.5 3l-3 3 .7 2.8 2.8.7z"/></svg></div>
      <h3>Wartung</h3>
      <p>Die notwendigen Wartungen an Ihrer Klimaanlage führen wir professionell durch</p>
    </div>
  </div>
  <footer class="footer">
    <ul class="contact" style="left:26px;top:38px">
      <li><svg width="14" height="16" viewBox="0 0 24 24"><path fill="var(--navy)" d="M6.6 2 10 6.5 7.8 9a14 14 0 0 0 7.2 7.2l2.5-2.2L22 17.4 19.5 21C10 21 3 14 3 4.5z"/></svg>04521/6620418</li>
      <li><svg width="15" height="12" viewBox="0 0 24 18"><path fill="var(--navy)" d="M0 0h24v18H0z"/><path fill="none" stroke="#fff" stroke-width="2" d="M1 1l11 9 11-9"/></svg>info@kuehlwerk-klima.de</li>
    </ul>
    <div class="brand" style="left:234px;top:42px">Kühlwerk</div>
  </footer>
</section>

<section class="flyer flyer--back">
  <p class="intro">Kühlwerk GmbH ist Ihr zuverlässiger Partner im Bereich <b>Klima-, Kälte- und Lüftungstechnik</b>. Als <em>zertifiziertes Fachunternehmen</em> bieten wir Ihnen schlüsselfertige Kälte-, Klima- und Lüftungsanlagen von marktführenden Herstellern. Von Installations- und Instandhaltungsleistungen bis zu Hygieneinspektionen nach <b>VDI 6022</b> steht unser zertifiziertes Fachpersonal Ihnen gerne zur Seite.</p>
  <div class="promise-area"></div>
  <div class="photo-circle photo-couple" role="img" aria-label="Foto: Monteur trägt ein Klimagerät ins Schlafzimmer, Frau freut sich auf dem Bett"></div>
  <div class="photo-circle photo-unit" role="img" aria-label="Foto: Wärmepumpe mit Innen- und Außeneinheit"></div>
  <div class="photo-circle photo-woman" role="img" aria-label="Foto: Lächelnde Frau hält ein Klimagerät"></div>
  <div class="promise">
    <h2>Unser Versprechen:</h2>
    <h3>Schnelle Installation</h3><p>Garantierte Installation innerhalb von wenigen Wochen</p>
    <h3>Festpreis</h3><p>Alle unsere Angebote zum Festpreis keine Änderung durch mehr Aufwand</p>
    <h3>Faire Preise</h3><p>Wir sind von fairen Preisen überzeugt und bieten ein faires Preis-/Leistungsverhältnis</p>
    <h3>Höchste Qualität</h3><p>Wir führen jede Arbeit mit höchster Sorgfalt und Qualität durch</p>
  </div>
  <div class="offer">
    <p>Fordern Sie<br>unverbindlich ein<br>Angebot ein:</p>
    <ul>
      <li><svg width="14" height="16" viewBox="0 0 24 24"><path fill="var(--navy)" d="M6.6 2 10 6.5 7.8 9a14 14 0 0 0 7.2 7.2l2.5-2.2L22 17.4 19.5 21C10 21 3 14 3 4.5z"/></svg>04521/6620418</li>
      <li><svg width="15" height="12" viewBox="0 0 24 18"><path fill="var(--navy)" d="M0 0h24v18H0z"/><path fill="none" stroke="#fff" stroke-width="2" d="M1 1l11 9 11-9"/></svg>info@kuehlwerk-klima.de</li>
    </ul>
  </div>
  <div class="brand" style="left:252px;top:1025px">Kühlwerk</div>
</section>

</body>
</html>
```